Irrigation Business needs their business cards modernised and revamped

I would like to keep my current logo, colours and revamp the format of the card.

I would like the card to be clean yet important.

Im not sure if you include texture but i would like the named logo to be indented into the card etc.

show me something alive and free something thats clinical to the point yet has a feel of achievement. i would like people to go nice card.

Target Market(s)

high end clients, corporate, sports field manger, the guys that make the decisions

Industry/Entity Type

Business

Contact Information for Business Card

nformation to be included

Dean Harlow (Director)
0487305526
dean@kolvat.biz
www.kestonfieldworks.com

instagram logo
google logo
facebook logo

Colors

Designer to choose colors to be used in the design.

Requirements
Nice to have
• indentations a really nice feel to the card good texture

```html
<!DOCTYPE html>
<html lang="en">
<head>
<meta charset="utf-8">
<title>Keston Fieldworks – Business Card</title>
<link href="https://fonts.googleapis.com/css2?family=Arimo:wght@400;700&display=swap" rel="stylesheet">
<style>
  :root {
    --backdrop: #2b2b2b;
    --card-white: #ffffff;
    --card-shade: #d9d9d9;
    --brand-blue: #1f5ba6;
    --brand-sky: #3aa6dc;
    --brand-green: #1e9447;
    --ink: #1a1a1a;
    --icon-blue: #2a5d9c;
    --seal-tint: #c9dcee;
    --seal-ring: #b7cbe6;
  }
  * { margin: 0; padding: 0; box-sizing: border-box; }
  html, body { width: 1200px; height: 997px; overflow: hidden; }
  body {
    background: var(--backdrop);
    font-family: "Arimo", Arial, sans-serif;
    position: relative;
  }
  .card {
    position: absolute;
    top: 274px;
    width: 532px;
    height: 319px;
    overflow: hidden;
  }
  .card--front {
    left: 70px;
    background: linear-gradient(90deg, var(--card-shade) 0%, #f1f1f1 35%, var(--card-white) 55%);
  }
  .card--back {
    left: 612px;
    background: linear-gradient(90deg, var(--card-white) 60%, #e6e6e6 100%);
  }
  .seal {
    position: absolute;
    width: 332px;
    height: 332px;
    border-radius: 50%;
    border: 12px solid var(--seal-ring);
    background: var(--seal-tint);
    opacity: 0.6;
    top: 0;
  }
  .card--front .seal { left: 372px; }
  .card--back .seal { left: -170px; }
  .brand {
    position: absolute;
    display: flex;
    flex-direction: column;
    align-items: center;
    color: var(--brand-blue);
    font-weight: 700;
    white-space: nowrap;
  }
  .brand__dot {
    border-radius: 50%;
    background: radial-gradient(circle at 50% 40%, var(--brand-sky) 0%, var(--brand-blue) 75%);
    border: 3px solid var(--brand-blue);
  }
  .card--front .brand { left: 113px; top: 18px; width: 300px; }
  .card--front .brand__dot { width: 70px; height: 70px; margin-bottom: 10px; }
  .card--front .brand__name { font-size: 21px; letter-spacing: -0.2px; }
  .card--back .brand { left: 190px; top: 83px; width: 300px; }
  .card--back .brand__dot { width: 96px; height: 96px; margin-bottom: 16px; }
  .card--back .brand__name { font-size: 28px; letter-spacing: -0.3px; }
  .brand__social {
    display: flex;
    gap: 10px;
    margin-top: 14px;
  }
  .brand__social span {
    width: 18px;
    height: 18px;
    border-radius: 50%;
    background: var(--icon-blue);
  }
  .contact {
    position: absolute;
    left: 28px;
    top: 174px;
    font-size: 13px;
    line-height: 16px;
  }
  .contact__name { color: var(--brand-blue); font-weight: 700; font-size: 14px; }
  .contact__role { color: var(--ink); font-weight: 700; }
  .contact__address { color: var(--brand-green); margin-top: 8px; }
  .contact__lines { list-style: none; margin-top: 10px; color: var(--ink); }
  .contact__lines li { display: flex; align-items: center; gap: 8px; height: 18px; }
  .contact__icon { width: 13px; height: 13px; flex: none; }
</style>
</head>
<body>
  <section class="card card--front" aria-label="Card front">
    <div class="seal"></div>
    <div class="brand">
      <span class="brand__dot"></span>
      <span class="brand__name">KESTON FIELDWORKS</span>
    </div>
    <div class="contact">
      <p class="contact__name">DEAN HARLOW</p>
      <p class="contact__role">Director</p>
      <p class="contact__address">PO Box 512 Marrindale<br>B.C. QLD 4360</p>
      <ul class="contact__lines">
        <li>
          <svg class="contact__icon" viewBox="0 0 16 16" aria-hidden="true">
            <circle cx="8" cy="8" r="8" fill="var(--icon-blue)"/>
            <path d="M4.5 6.5c0-1.2 1-2 3.5-2s3.5.8 3.5 2l-1.5.3-.3-1H6.3l-.3 1z M5.5 8h5l.8 3.5H4.7z" fill="#fff"/>
          </svg>
          0487305526
        </li>
        <li>
          <svg class="contact__icon" viewBox="0 0 16 16" aria-hidden="true">
            <circle cx="8" cy="8" r="8" fill="var(--icon-blue)"/>
            <rect x="4" y="5" width="8" height="6" fill="#fff"/>
            <path d="M4 5l4 3.2L12 5" fill="none" stroke="var(--icon-blue)" stroke-width="1"/>
          </svg>
          dean@kolvat.biz
        </li>
        <li>
          <svg class="contact__icon" viewBox="0 0 16 16" aria-hidden="true">
            <circle cx="8" cy="8" r="8" fill="var(--icon-blue)"/>
            <circle cx="8" cy="8" r="4.5" fill="none" stroke="#fff" stroke-width="1"/>
            <path d="M3.5 8h9M8 3.5c-2 2.5-2 6.5 0 9M8 3.5c2 2.5 2 6.5 0 9" fill="none" stroke="#fff" stroke-width="0.9"/>
          </svg>
          www.kestonfieldworks.com
        </li>
      </ul>
    </div>
  </section>

  <section class="card card--back" aria-label="Card back">
    <div class="seal"></div>
    <div class="brand">
      <span class="brand__dot"></span>
      <span class="brand__name">KESTON FIELDWORKS</span>
      <div class="brand__social" role="img" aria-label="Social media links">
        <span></span><span></span><span></span>
      </div>
    </div>
  </section>
</body>
</html>
```